Business card design for holistic health care clinic

We need a double-sided business card design for our holistic health care clinic that integrates our logo design and also its color scheme. My business is called Valmira. It is an integrative medicine clinic. You have already done the logo for me. Please ensure an elegant and upscale design that is not cluttered, but still has all the necessary information (please see below for details).

Target Market(s)

Wellness, fitness, rehabilitation for educated, well-traveled open-minded clients who are focused on natural, organic, balanced and preventive healthcare and lifestyle.

Industry/Entity Type

Medical

Contact Information for Business Card

Modern, clean.

Number of Pages Required

1 page

Font styles to use
Serif
Sans Serif

Colors

Designer to choose colors to be used in the design.

Requirements
Must have
• Logo on one side, all other information on the other side.
• Other information should include:
• Tobias Wrenfeld - DOE, CPT, LMT
• 4100 East Marrow Drive
• Austin, TX 78119
• 512 555 0148
• 818 555 0192
• info@ValmiraHealth.example
• t.wrenfeld@ValmiraHealth.example
Nice to have
• Darker background on front - but not totally black - shaded/dark gray.

```html
<!DOCTYPE html>
<html lang="en">
<head>
<meta charset="utf-8">
<title>Valmira – Business Card</title>
<link rel="stylesheet" href="https://fonts.googleapis.com/css2?family=Nunito:wght@400;600;700;800;900&display=swap">
<style>
  :root {
    --page-bg: #c4c4c4;
    --card-dark-top: #3a3a3b;
    --card-dark-bottom: #222223;
    --brand-blue: #0b8fd0;
    --card-blue: #0893d0;
    --ink-dark: #2b2b2d;
    --text-light: #f2f2f2;
  }
  * { margin: 0; padding: 0; box-sizing: border-box; }
  html, body {
    width: 1200px; height: 960px; overflow: hidden;
    background: var(--page-bg);
    font-family: "Nunito", sans-serif;
  }
  .canvas { position: relative; width: 1200px; height: 960px; }

  .card {
    position: absolute;
    width: 601px; height: 343px;
    border-radius: 22px;
    overflow: hidden;
  }
  .card--front {
    left: 302px; top: 116px;
    background: linear-gradient(180deg, var(--card-dark-top), var(--card-dark-bottom));
  }
  .card--back {
    left: 299px; top: 501px;
    background: var(--card-blue);
  }

  /* Front */
  .front-brand { position: absolute; left: 36px; top: 66px; color: var(--brand-blue); }
  .front-brand .brand-name {
    font-weight: 900; font-size: 52px; line-height: 1; letter-spacing: 1px;
    text-transform: uppercase;
  }
  .front-brand .brand-tagline {
    font-weight: 700; font-size: 15.5px; margin-top: 2px; margin-left: 3px;
  }
  .person { position: absolute; left: 38px; top: 222px; color: var(--brand-blue); }
  .person .person-name { font-weight: 800; font-size: 20px; letter-spacing: 0.5px; text-transform: uppercase; }
  .person .person-creds { font-weight: 800; font-size: 11px; letter-spacing: 0.6px; margin-top: 1px; }

  .contact {
    position: absolute; right: 41px; top: 184px;
    color: var(--text-light); text-align: right;
    font-size: 14.5px; font-weight: 600;
  }
  .contact .address { line-height: 17px; margin-bottom: 6px; }
  .contact-row {
    display: flex; justify-content: flex-end; align-items: center;
    height: 19.5px; gap: 8px;
  }
  .contact-row.small { font-size: 13.5px; }
  .contact-icon { width: 14px; height: 14px; fill: var(--brand-blue); flex: none; }

  /* Back */
  .back-brand {
    position: absolute; left: 0; right: 0; top: 128px;
    text-align: center; color: var(--ink-dark);
  }
  .back-brand .brand-name {
    font-weight: 900; font-size: 74px; line-height: 1; letter-spacing: 2px;
    text-transform: uppercase;
  }
  .back-brand .brand-tagline { font-weight: 700; font-size: 19px; margin-top: 2px; }
  .slogan {
    position: absolute; left: 134px; right: 134px; top: 280px;
    display: flex; align-items: center; gap: 4px;
    color: var(--ink-dark); font-size: 15px; font-weight: 600; white-space: nowrap;
  }
  .slogan .rule { flex: 1; height: 1px; background: var(--ink-dark); }
</style>
</head>
<body>
<main class="canvas">

  <section class="card card--front" aria-label="Card front">
    <div class="front-brand">
      <div class="brand-name">Valmira</div>
      <div class="brand-tagline">Integrative Holistic Medicine</div>
    </div>

    <div class="person">
      <div class="person-name">Tobias Wrenfeld</div>
      <div class="person-creds">DOE, CPT, LMT</div>
    </div>

    <div class="contact">
      <div class="address">4100 East Marrow Drive<br>Austin, TX 78119</div>
      <div class="contact-row">
        <span>512 555 0148</span>
        <svg class="contact-icon" viewBox="0 0 24 24" aria-hidden="true"><path d="M6.6 10.8a15.1 15.1 0 0 0 6.6 6.6l2.2-2.2c.3-.3.7-.4 1-.2 1.1.4 2.3.6 3.6.6.6 0 1 .4 1 1V20c0 .6-.4 1-1 1A17 17 0 0 1 3 4c0-.6.4-1 1-1h3.5c.6 0 1 .4 1 1 0 1.3.2 2.5.6 3.6.1.3 0 .7-.2 1z"/></svg>
      </div>
      <div class="contact-row">
        <span>818 555 0192</span>
        <svg class="contact-icon" viewBox="0 0 24 24" aria-hidden="true"><path d="M7 1h10a2 2 0 0 1 2 2v18a2 2 0 0 1-2 2H7a2 2 0 0 1-2-2V3a2 2 0 0 1 2-2zm0 3v15h10V4zm5 16.2a.9.9 0 1 0 0 1.8.9.9 0 0 0 0-1.8z"/></svg>
      </div>
      <div class="contact-row small">
        <span>t.wrenfeld@ValmiraHealth.example</span>
        <svg class="contact-icon" viewBox="0 0 24 24" aria-hidden="true"><path d="M2 5h20v14H2zm2 2v.5l8 5 8-5V7zm0 2.8V17h16V9.8l-8 5z"/></svg>
      </div>
      <div class="contact-row small">
        <span>www.ValmiraHealth.example</span>
        <svg class="contact-icon" viewBox="0 0 24 24" aria-hidden="true"><circle cx="12" cy="12" r="10"/></svg>
      </div>
    </div>
  </section>

  <section class="card card--back" aria-label="Card back">
    <div class="back-brand">
      <div class="brand-name">Valmira</div>
      <div class="brand-tagline">Integrative Holistic Medicine</div>
    </div>
    <div class="slogan">
      <span class="rule"></span>
      <span>helping the body help itself</span>
      <span class="rule"></span>
    </div>
  </section>

</main>
</body>
</html>
```